Business Cards for a law firm

Business cards for our law firm. Use our silhoette logo and OAK PARTNERS - check our website (www.oakpartners.example)

Contact Information for Business Card

our silhouette logo, OAK PARTNERS, 800-555-0147, Dorian Pemberton, dorian@oakpartners.example

Requirements
Must have
• our silhouette logo, OAK PARTNERS, 800-555-0147, Dorian Pemberton, dorian@oakpartners.example

```html
<!DOCTYPE html>
<html lang="en">
<head>
<meta charset="utf-8">
<title>Oak Partners – Business Cards</title>
<link rel="stylesheet" href="https://fonts.googleapis.com/css2?family=Montserrat:wght@400;800&family=Tenor+Sans&display=swap">
<style>
  :root {
    --stage: #e3e7e9;
    --navy: #233469;
    --navy-soft: #2c4183;
    --sky: #3a86cf;
    --paper: #ffffff;
  }
  * { margin: 0; padding: 0; box-sizing: border-box; }
  html, body { width: 1200px; height: 960px; overflow: hidden; }
  body { background: var(--stage); position: relative; }

  .card {
    position: absolute;
    top: 105px;
    width: 429px;
    height: 750px;
    border-radius: 28px;
    overflow: hidden;
  }
  .card--front { left: 142px; background: var(--navy); }
  .card--back  { left: 631px; background: var(--paper); }

  .front-art { position: absolute; inset: 0; }
  .front-wordmark {
    font-family: "Tenor Sans", sans-serif;
    font-size: 76px;
    fill: var(--sky);
  }

  .brand {
    position: absolute;
    top: 66px;
    left: 80px;
    display: flex;
    align-items: center;
    gap: 16px;
  }
  .brand__mark {
    width: 52px; height: 52px;
    border-radius: 50%;
    background: var(--navy);
  }
  .brand__name {
    font-family: "Tenor Sans", sans-serif;
    color: var(--navy);
    font-size: 34px;
    line-height: 0.9;
    letter-spacing: 0.5px;
  }

  .holder {
    position: absolute;
    top: 540px;
    left: 0; right: 0;
    text-align: center;
    font-family: "Montserrat", sans-serif;
    font-size: 28px;
    line-height: 32px;
    color: var(--navy);
    letter-spacing: 0.5px;
    white-space: nowrap;
  }
  .holder__first { font-weight: 800; }
  .holder__last  { font-weight: 400; }

  .contact-band {
    position: absolute;
    top: 604px;
    left: 0; right: 0; bottom: 0;
    background: var(--navy);
  }

  .contact-icons {
    position: absolute;
    top: 585px;
    left: 0; right: 0;
    display: flex;
    justify-content: center;
    gap: 9px;
  }
  .contact-icon { width: 34px; height: 34px; display: block; }

  .contact-list {
    position: absolute;
    top: 634px;
    left: 0; right: 0;
    list-style: none;
    text-align: center;
    font-family: "Tenor Sans", sans-serif;
    color: var(--paper);
    white-space: nowrap;
  }
  .contact-list li { line-height: 24.5px; letter-spacing: 1px; }
  .contact-list__phone { font-size: 21px; }
  .contact-list__web,
  .contact-list__mail { font-size: 15px; text-transform: uppercase; }
</style>
</head>
<body>

<section class="card card--front" aria-label="Card front">
  <svg class="front-art" viewBox="0 0 429 750" width="429" height="750">
    <text class="front-wordmark" transform="translate(198 521) rotate(-90)" textLength="181" lengthAdjust="spacing">OAK</text>
    <text class="front-wordmark" transform="translate(260 521) rotate(-90)" textLength="440" lengthAdjust="spacing">PARTNERS</text>
    <circle cx="211" cy="608" r="55" fill="var(--navy-soft)"/>
  </svg>
</section>

<section class="card card--back" aria-label="Card back">
  <div class="brand">
    <span class="brand__mark"></span>
    <p class="brand__name">OAK<br>PARTNERS</p>
  </div>

  <p class="holder"><span class="holder__first">DORIAN</span> <span class="holder__last">PEMBERTON</span></p>

  <div class="contact-band"></div>

  <div class="contact-icons">
    <svg class="contact-icon" viewBox="0 0 34 34" aria-label="Phone">
      <circle cx="17" cy="17" r="16" fill="var(--paper)" stroke="var(--navy)" stroke-width="2"/>
      <circle cx="17" cy="17" r="12.5" fill="var(--navy)"/>
      <path d="M12.5 11.5c1-1 2-1 2.5 0l1.2 2c.4.8 0 1.3-.6 1.8-.4.3-.3.8 0 1.3.7 1.1 1.6 2 2.7 2.7.5.3 1 .4 1.3 0 .5-.6 1-1 1.8-.6l2 1.2c1 .5 1 1.5 0 2.5-1.5 1.5-4 1-6.8-1.4-2.9-2.5-5.2-5.9-4.1-8.5.1-.4.1-.6 0-1z" fill="var(--paper)"/>
    </svg>
    <svg class="contact-icon" viewBox="0 0 34 34" aria-label="Email">
      <circle cx="17" cy="17" r="16" fill="var(--paper)" stroke="var(--navy)" stroke-width="2"/>
      <circle cx="17" cy="17" r="12.5" fill="var(--navy)"/>
      <rect x="10.5" y="12.5" width="13" height="9" fill="none" stroke="var(--paper)" stroke-width="1.3"/>
      <path d="M10.5 12.5 17 18l6.5-5.5" fill="none" stroke="var(--paper)" stroke-width="1.3"/>
    </svg>
    <svg class="contact-icon" viewBox="0 0 34 34" aria-label="Website">
      <circle cx="17" cy="17" r="16" fill="var(--paper)" stroke="var(--navy)" stroke-width="2"/>
      <circle cx="17" cy="17" r="12.5" fill="var(--navy)"/>
      <circle cx="17" cy="17" r="7" fill="none" stroke="var(--paper)" stroke-width="1.3"/>
      <ellipse cx="17" cy="17" rx="3" ry="7" fill="none" stroke="var(--paper)" stroke-width="1.1"/>
      <path d="M10 17h14" stroke="var(--paper)" stroke-width="1.1"/>
    </svg>
  </div>

  <ul class="contact-list">
    <li class="contact-list__phone">800-555-0147</li>
    <li class="contact-list__web">www.oakpartners.example</li>
    <li class="contact-list__mail">dorian@oakpartners.example</li>
  </ul>
</section>

</body>
</html>
```